Cedar Brook Stables, LLC

Equestrian business card to promote equine retirement, farm sitting, short term board. Located in Aiken, SC.
Updates
Updated color schemes.
Contact Information for Business Card
Contact info, description of work.
Colors
0094D4
00A9DD
6FCCEA
C7EBF8
E9F6FB
59FF00
82FF00
B8FF75
E3FFCB
F4FFEA
F0912C
F2A743
F7CA91
FBE8D2
FDF5EE

```html
<!DOCTYPE html>
<html lang="en">
<head>
<meta charset="utf-8">
<title>Cedar Brook Stables, LLC – Business Card</title>
<link rel="stylesheet" href="https://fonts.googleapis.com/css2?family=Poppins:wght@400;500;600&display=swap">
<style>
  :root {
    --backdrop: #e6e7e8;
    --card: #ffffff;
    --green: #1f7a1f;
    --ink: #333333;
    --text: #2b2b2b;
    --sun: #f2a743;
  }
  * { margin: 0; padding: 0; box-sizing: border-box; }
  html, body {
    width: 1200px; height: 900px; overflow: hidden;
    background: var(--backdrop);
    font-family: "Poppins", sans-serif;
  }
  .card {
    position: absolute;
    top: 217px;
    width: 308px; height: 499px;
    background: var(--card);
  }
  .card--front { left: 279px; border-radius: 0 70px 0 70px; }
  .card--back  { left: 617px; border-radius: 70px 0 70px 0; }

  .brand {
    position: absolute; left: 0; right: 0;
    display: flex; flex-direction: column; align-items: center;
  }
  .card--front .brand { top: 110px; }
  .card--back .brand  { top: 55px; }
  .brand__circle {
    width: 120px; height: 120px; border-radius: 50%;
    background: var(--sun);
  }
  .brand__name {
    margin-top: 22px;
    font-size: 15px; font-weight: 600; color: var(--ink);
    letter-spacing: 0.2px; white-space: nowrap;
  }

  .services {
    position: absolute; top: 340px; left: 0; right: 0;
    text-align: center; list-style: none;
    color: var(--green); font-size: 18px; font-weight: 500; line-height: 22.5px;
  }

  .contact {
    position: absolute; left: 32px; top: 300px; color: var(--text);
  }
  .contact__name {
    font-size: 20px; font-weight: 600; color: var(--green); line-height: 22px;
    text-transform: uppercase;
  }
  .contact__role { font-size: 15px; line-height: 18px; }
  .contact__lines { list-style: none; margin-top: 12px; }
  .contact__line {
    display: flex; align-items: center; gap: 8px;
    font-size: 14px; line-height: 18px;
  }
  .contact__icon { width: 13px; height: 13px; fill: var(--green); flex: none; }
  .contact__address { margin-top: 14px; font-size: 14px; line-height: 18px; font-style: normal; }
</style>
</head>
<body>
  <section class="card card--front">
    <div class="brand">
      <div class="brand__circle"></div>
      <p class="brand__name">CEDAR BROOK STABLES, LLC</p>
    </div>
    <ul class="services">
      <li>Short Term Board</li>
      <li>Farm sitting</li>
      <li>Equine Retirement</li>
    </ul>
  </section>

  <section class="card card--back">
    <div class="brand">
      <div class="brand__circle"></div>
      <p class="brand__name">CEDAR BROOK STABLES, LLC</p>
    </div>
    <div class="contact">
      <h1 class="contact__name">Daniel Hartley</h1>
      <p class="contact__role">Managing Director</p>
      <ul class="contact__lines">
        <li class="contact__line">
          <svg class="contact__icon" viewBox="0 0 24 24"><path d="M6.6 10.8a15 15 0 0 0 6.6 6.6l2.2-2.2a1 1 0 0 1 1-.25 11.4 11.4 0 0 0 3.6.57 1 1 0 0 1 1 1V20a1 1 0 0 1-1 1A17 17 0 0 1 3 4a1 1 0 0 1 1-1h3.5a1 1 0 0 1 1 1c0 1.25.2 2.45.57 3.6a1 1 0 0 1-.25 1z"/></svg>
          803-555 014 276
        </li>
        <li class="contact__line">
          <svg class="contact__icon" viewBox="0 0 24 24"><path d="M2 5h20v14H2z M2 5l10 8 10-8" fill="none" stroke="#1f7a1f" stroke-width="0"/><path d="M2 5h20v2l-10 7L2 7z"/><path d="M2 9l10 7 10-7v10H2z"/></svg>
          hello@cedarbrookstables.com
        </li>
        <li class="contact__line">
          <svg class="contact__icon" viewBox="0 0 24 24"><circle cx="12" cy="12" r="10" fill="none" stroke="#1f7a1f" stroke-width="2"/><ellipse cx="12" cy="12" rx="4" ry="10" fill="none" stroke="#1f7a1f" stroke-width="2"/><path d="M2 12h20M4 7h16M4 17h16" stroke="#1f7a1f" stroke-width="2"/></svg>
          www.cedarbrookstables.com
        </li>
      </ul>
      <address class="contact__address">118 Whiskey Road, Aiken<br>SC 29801, United States</address>
    </div>
  </section>
</body>
</html>
```